Electric mountain bike tours nz

We are an Electric Mountain bike tour company in New Zealand. We will be offering bike rental and guided tours around the Nelson region in New Zealand. I want our website to represent both Mountain biking and New Zealand with the colours layout and features. We want tabs for the following:
-1 about us
-2 what we offer
-3 bookings/contact
Under the about us tab will be who we are as a a company. I want the ability to add videos to each of these tabs as we move foward with videos of the tracks we will be riding. I want the website to be editable so I can add and remove videos/photos myself. Also "our bikes" will be under this tab.
Under the what we offer tab will be
-1 bike rental and pricing
-2 guided tours and pricing
-3 recommended package deals.
I want to able to put the tracks under the guided tours tab and select beginner/ intermediate/advanced and have the tracks in each of the following to match the rider level. Also to be able to have a small video of the track would be great in this section.
Bookings and contact tab
(Further information for this tab to be updated soon)
Coded - Design and coding required
1 page
- Silver ferns, kiwi, mountains

```html
<!DOCTYPE html>
<html lang="en">
<head>
<meta charset="utf-8">
<title>TRAILKNZ – Electric Bike Tours</title>
<link href="https://fonts.googleapis.com/css2?family=Roboto:ital,wght@0,400;0,500;0,700;0,900;1,400;1,700;1,900&display=swap" rel="stylesheet">
<style>
:root{
  --green:#1f7a31;
  --green-dark:#175f26;
  --orange:#f47c20;
  --blue:#2b52b3;
  --ink:#1b1b1b;
  --dark:#232323;
  --grey:#777;
  --light:#f3f3f3;
  --white:#fff;
}
*{box-sizing:border-box;margin:0;padding:0}
html,body{width:1200px;height:4534px;overflow:hidden}
body{font-family:"Roboto",sans-serif;color:var(--ink);background:var(--white);position:relative}
.abs{position:absolute}
.btn{position:absolute;display:flex;align-items:center;justify-content:center;border-radius:22px;font-size:13px;font-weight:700;text-transform:uppercase;letter-spacing:.3px}
.btn-green{background:var(--green);color:#fff}
.btn-white{background:#fff;color:var(--ink);border:2px solid var(--ink)}
.h-section{position:absolute;left:0;width:1200px;text-align:center;font-weight:900;font-style:italic;font-size:34px;text-transform:uppercase}
.ghost{position:absolute;left:0;width:1200px;text-align:center;font-weight:900;font-style:italic;font-size:74px;color:rgba(0,0,0,.06);text-transform:uppercase}

/* header */
.site-header{position:absolute;top:0;left:0;width:1200px;height:116px;background:#fff}
.brand{position:absolute;left:100px;top:10px;width:170px;height:60px;display:flex;align-items:center;gap:10px;font-weight:900;font-size:30px;color:var(--ink)}
.brand .dot{width:26px;height:26px;border-radius:50%;background:var(--ink)}
.nav{position:absolute;right:100px;top:62px;display:flex;gap:30px;font-size:14px;font-weight:700}
.nav .home-dot{position:absolute;left:6px;top:-28px;width:16px;height:16px;border-radius:50%;background:var(--ink)}

/* hero */
.hero{position:absolute;top:116px;left:0;width:1200px;height:590px;background:linear-gradient(135deg,#3b5a2a 0%,#6b6a3a 45%,#2d4a22 100%)}
.hero-title{position:absolute;left:97px;top:205px;color:#fff;font-size:40px;font-weight:900;font-style:italic}
.hero-text{position:absolute;left:97px;top:270px;width:500px;color:#fff;font-size:19px;line-height:1.5}
.arrow{position:absolute;font-size:24px;color:#fff}

/* welcome */
.intro{position:absolute;top:835px;left:280px;width:640px;text-align:center;font-size:12px;line-height:1.7;color:var(--grey)}
.card{position:absolute;top:918px;width:313px;height:300px;background:#fff;border:1px solid #ddd;box-shadow:0 2px 6px rgba(0,0,0,.2)}
.card .ph{position:absolute;left:10px;top:10px;width:291px;height:195px}
.card p{position:absolute;left:20px;top:228px;font-size:17px;font-weight:700;color:#555;line-height:1.5}

/* split */
.panel{position:absolute;top:1338px;height:495px;width:600px}
.panel-left{left:0;background:linear-gradient(180deg,#26405e,#121d2a);clip-path:polygon(0 0,100% 70px,100% 440px,0 100%)}
.panel-right{left:600px;background:linear-gradient(160deg,#2e8a3e,#17632a);clip-path:polygon(0 70px,100% 0,100% 100%,0 440px)}
.panel h3{position:absolute;top:125px;color:#fff;font-size:30px;font-weight:900;font-style:italic}
.panel p{position:absolute;top:190px;width:400px;color:#fff;font-size:12px;line-height:1.7}

/* packages */
.tabs{position:absolute;top:1922px;left:0;width:1200px;display:flex;justify-content:center;gap:28px;font-size:12px;font-weight:700}
.tabs span{padding:5px 10px}
.tabs .on{background:var(--ink);color:#fff}
.plan{position:absolute;background:var(--dark);color:#fff;text-align:center}
.plan .label{height:52px;display:flex;align-items:center;justify-content:center;font-size:26px;font-weight:900;font-style:italic}
.plan .price{position:relative;height:115px;clip-path:polygon(0 0,100% 0,100% 80%,0 100%);font-size:64px;font-weight:700;font-style:italic;display:flex;align-items:center;padding-left:90px}
.plan .price sup{font-size:24px;margin-top:-30px;margin-right:6px}
.plan .price small{font-size:14px;font-weight:400;margin-left:8px;margin-top:22px}
.plan h4{margin-top:22px;font-size:20px;font-weight:400;font-style:italic;text-transform:uppercase}
.plan ul{list-style:none;margin-top:24px}
.plan li{font-size:14px;line-height:51px}
.plan .btn{left:50%;transform:translateX(-50%);width:116px;height:38px}

/* banner */
.banner{position:absolute;top:2820px;left:0;width:1200px;height:395px;background:linear-gradient(180deg,#3a4d5e,#2e4a35 60%,#23361f)}
.banner h2{position:absolute;top:105px;width:1200px;text-align:center;color:#fff;font-size:38px;font-weight:900;font-style:italic;line-height:1.35}

/* about */
.about-ghost{position:absolute;left:0;top:3640px;transform-origin:0 0;transform:rotate(-90deg);font-size:64px;line-height:64px;font-weight:900;font-style:italic;color:rgba(0,0,0,.07);white-space:nowrap}
.about-title{position:absolute;left:100px;top:3302px;font-size:34px;font-weight:900;font-style:italic}
.about-text{position:absolute;left:100px;top:3368px;width:520px;font-size:13px;line-height:1.75;color:#666}
.video{position:absolute;left:690px;top:3355px;width:410px;height:262px;background:linear-gradient(160deg,#8fb3d8,#6b8a5a 55%,#3f5e2d)}
.video-frame{position:absolute;left:728px;top:3312px;width:416px;height:272px;border:3px solid var(--green)}
.play{position:absolute;left:870px;top:3461px}

/* testimonials */
.quote{position:absolute;top:3856px;width:300px}
.quote .face{position:absolute;left:0;top:0;width:64px;height:64px;border-radius:50%;background:linear-gradient(135deg,#b58a6a,#5a3e2e)}
.quote .stars{position:absolute;left:80px;top:0;color:#f4a820;font-size:15px;letter-spacing:2px}
.quote p{position:absolute;left:80px;top:24px;width:220px;font-size:12px;font-style:italic;line-height:1.6;color:#666}
.quote .who{position:absolute;left:0;top:140px;font-size:13px;font-weight:700}
.quote .role{position:absolute;left:0;top:162px;font-size:12px;color:#777;white-space:nowrap}

/* footer */
.site-footer{position:absolute;top:4155px;left:0;width:1200px;height:379px;background:#1a1a1a;color:#fff}
.site-footer h5{position:absolute;top:75px;font-size:16px;font-weight:500}
.links{position:absolute;top:118px;list-style:none;font-size:12px;line-height:32px}
.links li::before{content:"▸";margin-right:10px}
.copy{position:absolute;top:330px;width:1200px;text-align:center;font-size:13px}
</style>
</head>
<body>

<header class="site-header">
  <div class="brand"><span class="dot"></span>TRAILKNZ</div>
  <nav class="nav">
    <span style="position:relative"><i class="home-dot"></i>HOME</span>
    <span>ABOUT US</span><span>WHAT WE OFFER</span><span>BOOKINGS</span><span>CONTACT US</span>
  </nav>
</header>

<section class="hero" role="img" aria-label="Orange electric mountain bike on a forest trail beside a track sign">
  <h1 class="hero-title">ELECTRIC BIKE TOURS</h1>
  <p class="hero-text">Nemo enim ipsam voluptatem quia voluptas sit aspernatur aut odit aut fugit, sed quia consequuntur magni.</p>
  <span class="btn btn-green" style="left:97px;top:370px;width:162px;height:44px">READ MORE ➔</span>
  <span class="arrow" style="left:40px;top:275px">‹</span>
  <span class="arrow" style="right:40px;top:275px">›</span>
</section>

<section class="welcome">
  <div class="ghost" style="top:740px">WELCOME TO TRAILKNZ</div>
  <h2 class="h-section" style="top:770px;font-size:32px">WELCOME TO TRAILKNZ</h2>
  <p class="intro">At vero eos et accusamus et iusto odio dignissimos ducimus qui blanditiis praesentium voluptatum deleniti atque corrupti quos dolores et quas molestias excepturi sint occaecati cupiditate.</p>
  <div class="card" style="left:97px"><div class="ph" role="img" aria-label="Grey electric mountain bike" style="background:linear-gradient(180deg,#f4f4f4,#d8d8d8)"></div><p>The Summer Tours Feet Cycling<br>City Name, NZ</p></div>
  <div class="card" style="left:444px"><div class="ph" role="img" aria-label="Riders resting by a river with bikes" style="background:linear-gradient(160deg,#6f9a4a,#3d6a2e 60%,#7fa6c4)"></div><p>The Summer Tours Feet Cycling<br>City Name, NZ</p></div>
  <div class="card" style="left:790px"><div class="ph" role="img" aria-label="Black electric mountain bike" style="background:linear-gradient(180deg,#f4f4f4,#d8d8d8)"></div><p>The Summer Tours Feet Cycling<br>City Name, NZ</p></div>
  <span class="btn btn-green" style="left:405px;top:1266px;width:185px;height:46px">BOOK YOUR BIKE</span>
  <span class="btn btn-white" style="left:608px;top:1266px;width:188px;height:46px">DOWNLOAD GUIDE</span>
</section>

<section class="split">
  <div class="panel panel-left" role="img" aria-label="Mountain bike overlooking a coastal bay">
    <h3 style="left:97px">BIKE RENTAL</h3>
    <p style="left:97px">At vero eos et accusamus et iusto odio dignissimos ducimus qui blanditiis praesentium voluptatum deleniti atque corrupti quos dolores et quas molestias excepturi sint occaecati cupiditate non provident, similique sunt in culpa qui officia deserunt.</p>
    <span class="btn btn-green" style="left:97px;top:318px;width:150px;height:42px">BOOK NOW ➔</span>
  </div>
  <div class="panel panel-right">
    <h3 style="left:100px">TOURS GUIDE</h3>
    <p style="left:100px">At vero eos et accusamus et iusto odio dignissimos ducimus qui blanditiis praesentium voluptatum deleniti atque corrupti quos dolores et quas molestias excepturi sint occaecati cupiditate non provident, similique sunt in culpa qui officia deserunt.</p>
    <span class="btn btn-white" style="left:100px;top:318px;width:150px;height:42px;border:none">DOWNLOAD ➔</span>
  </div>
</section>

<section class="packages">
  <div class="ghost" style="top:1835px">OUR PACKAGES</div>
  <h2 class="h-section" style="top:1860px;font-size:32px">OUR PACKAGES</h2>
  <div class="tabs"><span>BIKE RENTAL</span><span>GUIDED TOURS</span><span class="on">RECOMMENDED</span></div>

  <div class="plan" style="left:100px;top:2038px;width:334px;height:618px">
    <div class="label" style="background:var(--orange)">STARTER</div>
    <div class="price" style="background:#f8913e"><sup>$</sup>19<small>/ MONTH</small></div>
    <h4>Single Place Travel</h4>
    <ul><li>Lorem ipsum doloret</li><li>At vero eos et accusamus</li><li>Nam libero tempore coluta</li><li>Excepteur sint occaecat</li><li>On the other had esounce</li></ul>
    <span class="btn btn-green" style="top:545px">BOOK NOW</span>
  </div>
  <div class="plan" style="left:434px;top:2008px;width:332px;height:676px">
    <div class="label" style="background:var(--green-dark);height:58px">STANDARD</div>
    <div class="price" style="background:var(--green);height:140px"><sup>$</sup>39<small>/ MONTH</small></div>
    <h4>Three Place Travel</h4>
    <ul><li>Nam libero tempore coluta</li><li>On the other had esounce</li><li>Lorem ipsum doloret</li><li>At vero eos et accusamus</li><li>Excepteur sint occaecat</li></ul>
    <span class="btn btn-green" style="top:600px">BOOK NOW</span>
  </div>
  <div class="plan" style="left:766px;top:2038px;width:334px;height:618px">
    <div class="label" style="background:var(--blue)">ULTIMATE</div>
    <div class="price" style="background:#3c64c8"><sup>$</sup>59<small>/ MONTH</small></div>
    <h4>Five Place Travel</h4>
    <ul><li>Excepteur sint occaecat</li><li>Nam libero tempore coluta</li><li>At vero eos et accusamus</li><li>On the other had esounce</li><li>Lorem ipsum doloret</li></ul>
    <span class="btn btn-green" style="top:545px">BOOK NOW</span>
  </div>
</section>

<section class="banner" role="img" aria-label="Forested hills above a New Zealand harbour">
  <h2>BOOK YOUR ELECTRIC BIKE TOURS<br>IN NEW ZEALAND</h2>
  <span class="btn btn-green" style="left:520px;top:240px;width:160px;height:42px">BOOK NOW ➔</span>
</section>

<section class="about">
  <div class="about-ghost">ABOUT US</div>
  <h2 class="about-title">TRAVEL FURTHER AND FASTER</h2>
  <p class="about-text">Sed ut perspiciatis unde omnis iste natus error sit voluptatem accusantium doloremque laudantium, totam rem aperiam, eaque ipsa quae ab illo.<br><br>Inventore veritatis et quasi architecto beatae vitae dicta sunt explicabo. Nemo enim ipsam voluptatem quia voluptas sit aspernatur aut odit aut fugit, sed quia consequuntur magni dolores eos qui ratione voluptatem sequi nesciunt. Neque porro quisquam est, qui dolorem ipsum quia dolor sit amet, consectetur, adipisci velit.</p>
  <span class="btn btn-green" style="left:100px;top:3580px;width:160px;height:44px">READ MORE ➔</span>
  <div class="video-frame"></div>
  <div class="video" role="img" aria-label="Video of a rider on an alpine valley track"></div>
  <svg class="play" width="56" height="56" viewBox="0 0 56 56" aria-label="Play video"><circle cx="28" cy="28" r="26" fill="rgba(255,255,255,.9)"/><path d="M23 18 L38 28 L23 38Z" fill="var(--green)"/></svg>
</section>

<section class="testimonials">
  <div class="abs" style="left:100px;top:3722px;width:1000px;border-top:1px solid #ddd"></div>
  <h2 class="h-section" style="top:3782px">TESTIMONIALS</h2>
  <div class="quote" style="left:100px"><div class="face" role="img" aria-label="Customer portrait"></div><div class="stars">★★★★☆</div><p>“ At vero eos et accusamus et iusto odio dignissimos ducimus qui blanditiis praesentium voluptatum deleniti atque corrupti quos dolores ”</p><div class="who">MARA LIND</div><div class="role">Creative Manager, NZ</div></div>
  <div class="quote" style="left:445px"><div class="face" role="img" aria-label="Customer portrait"></div><div class="stars">★★★★☆</div><p>“ At vero eos et accusamus et iusto odio dignissimos ducimus qui blanditiis praesentium voluptatum deleniti atque corrupti quos dolores ”</p><div class="who">TOM KELLER</div><div class="role">Events Manager, NZ</div></div>
  <div class="quote" style="left:795px"><div class="face" role="img" aria-label="Customer portrait"></div><div class="stars">★★★★☆</div><p>“ At vero eos et accusamus et iusto odio dignissimos ducimus qui blanditiis praesentium voluptatum deleniti atque corrupti quos dolores ”</p><div class="who">ANA REID</div><div class="role">Sports Manager, NZ</div></div>
  <span class="abs" style="left:25px;top:3960px;font-size:26px;color:#777">‹</span>
  <span class="abs" style="right:25px;top:3960px;font-size:26px;color:#777">›</span>
  <svg class="abs" style="left:578px;top:4075px" width="44" height="12"><circle cx="6" cy="6" r="4" fill="none" stroke="#333"/><circle cx="22" cy="6" r="4" fill="#333"/><circle cx="38" cy="6" r="4" fill="none" stroke="#333"/></svg>
</section>

<footer class="site-footer">
  <div class="abs" style="left:130px;top:110px;display:flex;align-items:center;gap:8px;font-weight:900;font-size:24px"><span style="width:20px;height:20px;border-radius:50%;background:#fff"></span>TRAILKNZ</div>
  <svg class="abs" style="left:95px;top:245px" width="190" height="28" aria-label="Social links">
    <circle cx="12" cy="14" r="10" fill="#fff"/><circle cx="50" cy="14" r="10" fill="#fff"/><circle cx="88" cy="14" r="10" fill="var(--green)"/><circle cx="126" cy="14" r="10" fill="#fff"/><circle cx="164" cy="14" r="10" fill="#fff"/>
  </svg>
  <h5 style="left:415px">QUICK LINKS</h5>
  <ul class="links" style="left:415px"><li>Home</li><li>About Us</li><li>What We Offer</li><li>Tour Guide</li><li>Contact Us</li></ul>
  <ul class="links" style="left:590px"><li>Info</li><li>Blog Post</li><li>Press</li><li>Privacy Policy</li><li>Terms of Service</li></ul>
  <h5 style="left:828px">NEWSLETTER SUBSCRIPTION</h5>
  <p class="abs" style="left:828px;top:118px;width:270px;font-size:12px;line-height:1.5">Register your Email Address to get a more information about us</p>
  <div class="abs" style="left:828px;top:170px;width:272px;height:36px;background:#fff;color:#999;font-size:12px;padding:11px 12px">Email</div>
  <span class="btn btn-green" style="left:828px;top:222px;width:104px;height:34px;font-size:12px">SUBSCRIBE</span>
  <div class="abs" style="left:100px;top:305px;width:1000px;border-top:1px solid #444"></div>
  <p class="copy">Copyrights © 2018 TRAILKNZ. All Rights Reserved.</p>
</footer>

</body>
</html>
```